Vantro cards

I am in the auto motive, transportation business I would like a business card that is Something cool, modern edgy, having to do with car culture. I offer towing service for high and exotic cars. I also provide towing for collisions and car accidents. I offer open and enclosed transport nationwide.

Target Market(s)

Car culture people high end auto collectors

Industry/Entity Type

Towing car carrier

Contact Information for Business Card

My company colors black yellow and silver

Font styles to use
Serif

```html
<!DOCTYPE html>
<html lang="en">
<head>
<meta charset="utf-8">
<title>Vantro Transportation – Business Cards</title>
<link rel="stylesheet" href="https://fonts.googleapis.com/css2?family=Arimo:wght@400;700&display=swap">
<style>
  :root {
    --backdrop: #e9e9e9;
    --card: #2f2f30;
    --card-back: #2a2a2b;
    --edge: #e8c22a;
    --yellow: #f2cf2a;
    --white: #f4f4f4;
    --silver: #b9b9b9;
    --rule: #8a8a8a;
    --truck-dark: #141414;
    --truck-mid: #3c3c3c;
  }
  * { box-sizing: border-box; margin: 0; padding: 0; }
  html, body { width: 1200px; height: 802px; overflow: hidden; }
  body {
    background: var(--backdrop);
    font-family: "Arimo", Arial, sans-serif;
    display: flex;
    align-items: center;
    justify-content: center;
    gap: 40px;
  }
  .card {
    position: relative;
    width: 560px;
    height: 320px;
    background: var(--card);
    border-bottom: 3px solid var(--edge);
    border-left: 3px solid var(--edge);
    box-shadow: 0 10px 24px rgba(0,0,0,.18);
    overflow: hidden;
  }
  /* Front */
  .brand {
    position: absolute;
    left: 48px; top: 78px;
    display: flex; align-items: center; gap: 12px;
  }
  .brand-mark { width: 18px; height: 18px; background: var(--yellow); }
  .brand-name {
    font-weight: 700; font-size: 40px; letter-spacing: 2px;
    color: var(--white);
  }
  .person {
    position: absolute;
    right: 300px; top: 190px;
    text-align: right;
  }
  .person-name { color: var(--yellow); font-size: 20px; font-weight: 700; letter-spacing: .5px; }
  .person-role { color: var(--silver); font-size: 15px; margin-top: 4px; }
  .divider {
    position: absolute; left: 276px; top: 150px;
    width: 1px; height: 96px; background: var(--rule);
  }
  .contacts {
    position: absolute; left: 296px; top: 150px;
    list-style: none;
  }
  .contacts li {
    display: flex; align-items: center; gap: 9px;
    color: var(--white); font-size: 15px; line-height: 30px;
  }
  .contacts svg { width: 13px; height: 13px; flex: none; }
  .address {
    position: absolute; left: 296px; top: 262px;
    color: var(--white); font-size: 15px;
  }
  /* Back */
  .card-back { background: var(--card-back); }
  .back-brand {
    position: absolute; left: 36px; top: 150px;
    display: flex; align-items: center; gap: 10px;
  }
  .back-brand .brand-name { color: var(--yellow); font-size: 34px; }
  .truck-art {
    position: absolute; right: 0; bottom: 0;
    width: 360px; height: 220px;
    background: linear-gradient(100deg, var(--truck-dark) 0%, var(--truck-dark) 40%, var(--truck-mid) 100%);
    border-top-left-radius: 40px;
  }
</style>
</head>
<body>
  <section class="card card-front">
    <div class="brand">
      <span class="brand-mark"></span>
      <span class="brand-name">VANTRO</span>
    </div>
    <div class="person">
      <p class="person-name">MARCUS HALE</p>
      <p class="person-role">Manager</p>
    </div>
    <div class="divider"></div>
    <ul class="contacts">
      <li>
        <svg viewBox="0 0 16 16" aria-hidden="true"><path fill="#f2cf2a" d="M3.6 1.5l2.3 2.3-1.4 1.9c.9 2 2.5 3.6 4.5 4.5l1.9-1.4 2.3 2.3-1.6 2.4C6.5 13.3 2.7 9.5 1.2 3.1z"/></svg>
        555-014-2100
      </li>
      <li>
        <svg viewBox="0 0 16 16" aria-hidden="true"><rect x="1" y="3" width="14" height="10" fill="#f2cf2a"/><path d="M1 3l7 6 7-6" fill="none" stroke="#2f2f30" stroke-width="1.4"/></svg>
        hello@vantromail.com
      </li>
      <li>
        <svg viewBox="0 0 16 16" aria-hidden="true"><circle cx="8" cy="8" r="7" fill="#f2cf2a"/><path d="M1 8h14M8 1c-3 3.5-3 10.5 0 14M8 1c3 3.5 3 10.5 0 14" fill="none" stroke="#2f2f30" stroke-width="1.2"/></svg>
        www.vantrotransport.com
      </li>
    </ul>
    <p class="address">Your Address, City, State, Zip 0000</p>
  </section>

  <section class="card card-back">
    <div class="back-brand">
      <span class="brand-name">VANTRO</span>
    </div>
    <div class="truck-art" role="img" aria-label="Embossed flatbed tow truck silhouette in black on dark grey"></div>
  </section>
</body>
</html>
```